Kestrel Facilities Business Card Design

We would now like to design business cards with the new Kestrel Facilities logo

Target Market(s)

Professional

Industry/Entity Type

Professional services

Contact Information for Business Card

Employee name, title, phone number, email address, corporate office address and logo.

Font styles to use
Sans Serif

Colors
0054AA
0677BA
7BADD7
CADEEF
E8F1F8

Requirements
Must have
• My logo
Should not have
• any other pictures or images besides my logo

```html
<!DOCTYPE html>
<html lang="en">
<head>
<meta charset="utf-8">
<title>Kestrel Facilities Business Card</title>
<link href="https://fonts.googleapis.com/css2?family=Montserrat:wght@400;500;600;700&display=swap" rel="stylesheet">
<style>
  :root {
    --bg: #2a2a2a;
    --card: #ffffff;
    --brand: #2f6fbe;
    --brand-deep: #0054aa;
    --tint: #e8f1f8;
    --ink: #1e1e1e;
    --muted: #333333;
  }
  * { box-sizing: border-box; margin: 0; padding: 0; }
  html, body { width: 1200px; height: 960px; overflow: hidden; }
  body {
    background: var(--bg);
    font-family: "Montserrat", Arial, sans-serif;
    position: relative;
  }
  .card {
    position: absolute;
    width: 630px;
    height: 360px;
    background: var(--card);
    border-radius: 22px;
    box-shadow: 0 14px 30px rgba(0,0,0,0.45);
    overflow: hidden;
  }
  .card--front { left: 70px; top: 60px; }
  .card--back { left: 500px; top: 540px; }

  .brand {
    display: flex;
    align-items: center;
    gap: 12px;
    color: var(--brand);
    font-weight: 700;
    letter-spacing: 0.04em;
    text-transform: uppercase;
  }
  .brand__mark {
    background: var(--brand);
    flex: none;
  }
  .card--front .brand {
    position: absolute;
    left: 50%; top: 50%;
    transform: translate(-50%, -50%);
    font-size: 34px;
  }
  .card--front .brand__mark { width: 30px; height: 30px; }

  .card--back .brand {
    position: absolute;
    left: 36px; top: 42px;
    font-size: 22px;
  }
  .card--back .brand__mark { width: 20px; height: 20px; }

  .holder {
    position: absolute;
    right: 40px; top: 70px;
    text-align: right;
  }
  .holder__name {
    color: var(--brand);
    font-weight: 700;
    font-size: 24px;
    letter-spacing: 0.03em;
    text-transform: uppercase;
  }
  .holder__title {
    color: var(--ink);
    font-size: 15px;
    margin-top: 4px;
  }

  .address {
    position: absolute;
    left: 36px; top: 150px;
    color: var(--ink);
    font-size: 16px;
    line-height: 1.4;
  }
  .contacts {
    position: absolute;
    left: 36px; top: 228px;
    list-style: none;
    color: var(--ink);
    font-size: 16px;
    line-height: 1;
  }
  .contacts li {
    display: flex;
    align-items: center;
    gap: 10px;
    margin-bottom: 11px;
  }
  .contacts svg { width: 16px; height: 16px; flex: none; }
</style>
</head>
<body>

  <section class="card card--front" aria-label="Business card front">
    <div class="brand"><span class="brand__mark"></span>Kestrel Facilities</div>
  </section>

  <section class="card card--back" aria-label="Business card back">
    <div class="brand"><span class="brand__mark"></span>Kestrel Facilities</div>

    <div class="holder">
      <p class="holder__name">Amani Otieno</p>
      <p class="holder__title">Co-Founder</p>
    </div>

    <p class="address">P.O Box 4410-00100<br>Nairobi, Kenya</p>

    <ul class="contacts">
      <li>
        <svg viewBox="0 0 16 16" aria-hidden="true"><path fill="#2f6fbe" d="M2 4c0-1.5 1.5-2.5 6-2.5S14 2.5 14 4v1.5h-3V4.2H5v1.3H2zM4 6.5h8l2 7.5H2z"/></svg>
        +254-100-55501
      </li>
      <li>
        <svg viewBox="0 0 16 16" aria-hidden="true"><rect x="1" y="3" width="14" height="10" fill="#2f6fbe"/><path d="M1.5 3.5 8 9l6.5-5.5" stroke="#fff" stroke-width="1.3" fill="none"/></svg>
        info@kestrelfacilities.com
      </li>
      <li>
        <svg viewBox="0 0 16 16" aria-hidden="true"><circle cx="8" cy="8" r="7" fill="#2f6fbe"/><path d="M1 8h14M8 1c-3 3.5-3 10.5 0 14M8 1c3 3.5 3 10.5 0 14" stroke="#fff" stroke-width="1" fill="none"/></svg>
        www.kestrelfacilities.com
      </li>
    </ul>
  </section>

</body>
</html>
```